NimbaVault Website Homepage Design

Please provide your idea of homepage for a hosting company. This project is for DESIGN only, no coding.

It must use/combine colors used in logo, clean, modern look.

Homepage must consist of at least 4 sections (example: testimonials, services, and so on. not necesarily all of them). We would like the navigation to be horizontal, but not mandatory.

You can include a preview of services page (optional, not a must).

Number of Pages Required

1 page

Font styles to use
Sans Serif

```html
<!DOCTYPE html>
<html lang="en">
<head>
<meta charset="utf-8">
<title>NimbaVault — Hosting</title>
<link href="https://fonts.googleapis.com/css2?family=Poppins:wght@300;400;500;600;700&display=swap" rel="stylesheet">
<style>
:root{
  --blue:#0a84de;
  --ink:#16202e;
  --text:#6b7380;
  --muted:#9aa1ab;
  --light:#f1f5fc;
  --line:#e6ebf2;
  --white:#fff;
  --footer:#0f1722;
  --footer-bar:#0c2340;
  --grey-btn:#9ea4ad;
  --step:#8f959d;
  --quote:#c6d7ef;
}
*{box-sizing:border-box;margin:0;padding:0}
html,body{width:1200px;height:5008px;overflow:hidden}
body{font-family:'Poppins',sans-serif;color:var(--text);background:var(--white);position:relative;font-size:13px}
.abs{position:absolute;left:0;width:1200px}
.wrap{width:952px;margin:0 auto;position:relative}
.blue{color:var(--blue)}
.btn{display:inline-flex;align-items:center;justify-content:center;border-radius:20px;font-size:12px;font-weight:500;color:var(--white);background:var(--blue);white-space:nowrap}
.sec-title{text-align:center;font-size:35px;font-weight:600;color:var(--ink);letter-spacing:-.3px}
.sec-lead{text-align:center;font-size:15px;line-height:27px;color:var(--text);width:640px;margin:14px auto 0}

/* top bar */
.topbar{top:0;height:33px;background:var(--blue);color:var(--white);font-size:10px;display:flex;align-items:center;justify-content:space-between;padding:0 35px}
.topbar span{display:inline-flex;align-items:center;gap:6px;white-space:nowrap}
.topbar .right{display:flex;gap:30px}

/* header */
.header{top:33px;height:80px;background:var(--white);white-space:nowrap}
.header > *{position:absolute;top:50%;transform:translateY(-50%)}
.logo{left:35px;font-size:24px;font-weight:600;color:var(--blue);letter-spacing:.5px}
.lang{left:188px;font-size:12px;font-weight:600;color:var(--ink);display:flex;align-items:center;gap:5px}
.nav{left:418px;display:flex;gap:30px;font-size:12px;font-weight:500;color:var(--ink)}
.nav .on{color:var(--blue)}
.search{left:826px}
.call{left:872px;display:flex;align-items:center;gap:12px}
.call b{display:block;color:var(--blue);font-size:13px;font-weight:500}
.call small{font-size:10px;color:var(--muted)}
.livechat{left:1050px;width:117px;height:40px;font-size:13px}

.dropdown{top:113px;left:478px;width:172px;height:198px;background:var(--white);box-shadow:0 6px 20px rgba(20,40,80,.12);padding:12px 18px;font-size:10px;color:var(--text);line-height:24px;z-index:3;white-space:nowrap}

/* hero */
.hero{top:113px;height:557px;background:var(--light)}
.hero h1{position:absolute;left:124px;top:118px;font-size:46px;line-height:56px;font-weight:600;color:var(--blue)}
.hero p{position:absolute;left:124px;top:245px;width:470px;font-size:17px;line-height:28px}
.hero .btns{position:absolute;left:124px;top:330px;display:flex;gap:16px}
.hero .btns .btn{width:146px;height:40px}
.hero .btns .grey{background:var(--grey-btn)}
.hero-art{position:absolute;left:710px;top:55px;width:370px;height:395px;border-radius:30px;background:radial-gradient(circle at 60% 45%,#cfe3fb,#e4eefb 60%,var(--light))}

/* pricing */
.pricing{top:599px;height:480px}
.plans{display:grid;grid-template-columns:repeat(3,1fr);background:var(--white);box-shadow:0 10px 30px rgba(20,40,80,.08);height:480px}
.plan{padding:42px 36px;border-right:1px solid var(--line)}
.plan:last-child{border:none}
.plan h3{font-size:22px;font-weight:600;color:var(--blue)}
.plan h3 span{font-weight:300;color:var(--muted)}
.plan .desc{font-size:11px;line-height:19px;margin-top:12px}
.price-row{display:flex;align-items:flex-end;justify-content:space-between;margin-top:38px}
.price{display:flex;align-items:baseline;gap:4px}
.price s{font-size:20px;color:var(--muted)}
.price b{font-size:34px;font-weight:600;color:var(--blue)}
.price small{font-size:11px;color:var(--muted)}
.sale{text-align:right;font-size:9px;line-height:16px}
.sale b{color:var(--blue);font-weight:600}
.specs-list{list-style:none;margin-top:42px;font-size:10px;line-height:26px}
.specs-list li{display:flex;align-items:center;gap:10px;white-space:nowrap}
.specs-list b{color:var(--ink);font-weight:600}
.plan .btn{width:146px;height:40px;margin-top:26px}

/* features */
.features{top:1147px;height:865px;background:var(--light);padding-top:88px}
.feat-grid{display:grid;grid-template-columns:repeat(3,303px);gap:15px 22px;margin-top:54px}
.feat{background:var(--white);height:241px;text-align:center;padding:22px 30px 0}
.feat.active{border-bottom:4px solid var(--blue)}
.icon-ring{width:82px;height:82px;border-radius:50%;border:2px solid var(--blue);margin:0 auto;display:flex;align-items:center;justify-content:center}
.feat h4{font-size:18px;font-weight:600;color:var(--ink);margin-top:12px}
.feat p{font-size:11px;line-height:18px;margin-top:8px}

/* specifications */
.specs{top:2012px;height:642px;padding-top:84px}
.spec-body{display:flex;gap:30px;margin-top:58px}
.tabs{width:212px;display:flex;flex-direction:column;gap:18px;padding-top:6px}
.tab{height:50px;background:var(--white);box-shadow:0 3px 12px rgba(20,40,80,.08);display:flex;align-items:center;padding-left:14px;font-size:12px;font-weight:500;color:var(--ink)}
.tab.on{color:var(--blue);border-left:3px solid var(--blue)}
.spec-grid{display:grid;grid-template-columns:345px 345px;gap:15px 19px}
.spec{height:136px;border:1px solid var(--line);padding:22px 20px;display:flex;gap:16px}
.spec svg{flex:none}
.spec h5{font-size:16px;font-weight:600;color:var(--ink);white-space:nowrap}
.spec p{font-size:11px;line-height:18px;margin-top:8px}

/* services */
.services{top:2654px;height:719px;background:var(--light);padding-top:92px}
.svc-grid{display:grid;grid-template-columns:repeat(3,303px);gap:22px;margin-top:54px}
.svc{background:var(--white);height:305px;text-align:center;padding:30px 30px 0}
.svc h4{font-size:18px;font-weight:600;color:var(--ink);padding-bottom:12px;border-bottom:1px solid var(--line)}
.svc .dot{width:82px;height:82px;border-radius:50%;background:var(--blue);margin:22px auto 0;display:flex;align-items:center;justify-content:center}
.svc p{font-size:11px;line-height:18px;margin-top:18px}
.svc a{display:block;font-size:11px;color:var(--blue);margin-top:20px;text-decoration:none}
.dots{display:flex;justify-content:center;gap:6px;margin-top:30px;align-items:center}
.dots i{width:6px;height:6px;border-radius:50%;background:var(--ink)}
.dots i.wide{width:22px;border-radius:3px;background:var(--blue)}

/* process */
.process{top:3373px;height:525px;padding-top:90px}
.steps{display:flex;justify-content:space-between;margin-top:70px;position:relative}
.step{width:290px;text-align:center}
.step .circle{width:100px;height:100px;border-radius:50%;background:var(--step);margin:0 auto;position:relative;display:flex;align-items:center;justify-content:center}
.step .num{position:absolute;top:-4px;right:-6px;width:30px;height:30px;border-radius:50%;background:var(--blue);color:var(--white);font-size:11px;border:3px solid var(--white);display:flex;align-items:center;justify-content:center}
.step h4{font-size:18px;font-weight:600;color:var(--ink);margin-top:22px;white-space:nowrap}
.step p{font-size:11px;line-height:18px;margin-top:8px}
.arrow{position:absolute;top:40px}

/* guarantee */
.guarantee{top:3898px;height:165px;background:var(--blue);color:var(--white)}
.guarantee h2{position:absolute;left:148px;top:44px;font-size:34px;font-weight:600}
.guarantee p{position:absolute;left:148px;top:102px;font-size:12px;font-weight:500}
.guarantee .btn{position:absolute;left:910px;top:64px;width:146px;height:40px;background:var(--white);color:var(--blue)}

/* testimonials */
.clients{top:4063px;height:613px;padding-top:82px}
.quotes{display:grid;grid-template-columns:repeat(3,303px);gap:22px;margin-top:56px}
.quote{background:var(--light);height:234px;padding:26px 16px 0;position:relative}
.quote h5{font-size:17px;font-weight:500;color:var(--ink)}
.quote small{font-size:10px;color:var(--blue)}
.quote .avatar{position:absolute;right:22px;top:16px;width:64px;height:64px;border-radius:50%;background:linear-gradient(135deg,#d9e4f2,#eef3fa)}
.quote p{font-size:11px;line-height:19px;margin-top:40px;text-align:justify}
.quote .mark{position:absolute;right:22px;bottom:14px;font-size:50px;line-height:40px;color:var(--quote);font-weight:700}

/* footer */
.footer{top:4676px;height:262px;background:var(--footer);color:#d6dbe2}
.fcol{position:absolute;top:52px;font-size:11px;line-height:24px}
.fcol h6{font-size:18px;font-weight:500;color:var(--blue);margin-bottom:12px}
.fcol ul{list-style:none}
.fcol li{white-space:nowrap}
.about{left:33px;width:260px}
.about .logo{position:static;transform:none;color:var(--white);display:block;margin-bottom:14px}
.about p{line-height:18px;color:var(--white)}
.cards{display:flex;gap:6px;margin-top:14px}
.cards span{width:44px;height:24px;background:var(--white);border-radius:3px;font-size:8px;font-weight:600;color:var(--ink);display:flex;align-items:center;justify-content:center}
.contact li{display:flex;gap:12px;align-items:flex-start;line-height:18px;margin-bottom:14px;white-space:normal}
.contact svg{flex:none;margin-top:3px}
.footbar{top:4938px;height:70px;background:var(--footer-bar);color:#d6dbe2;display:flex;align-items:center;justify-content:space-between;padding:0 33px;font-size:11px}
.social{display:flex;gap:12px}
.social i{width:28px;height:28px;border-radius:50%;background:var(--white);display:block}
</style>
</head>
<body>

<div class="abs topbar">
  <span><svg width="12" height="10" viewBox="0 0 12 10"><rect x=".5" y=".5" width="11" height="9" fill="none" stroke="#fff"/><path d="M.5 .5 6 5.5 11.5.5" fill="none" stroke="#fff"/></svg>hello@nimbavault.test</span>
  <div class="right"><span>LOGIN</span><span>SUPPORT</span><span>CART</span></div>
</div>

<header class="abs header">
  <div class="logo">NimbaVault</div>
  <div class="lang"><svg width="12" height="12" viewBox="0 0 12 12"><circle cx="6" cy="6" r="5" fill="none" stroke="#16202e"/><path d="M1 6h10M6 1c-3 3-3 7 0 10M6 1c3 3 3 7 0 10" fill="none" stroke="#16202e"/></svg>US</div>
  <nav class="nav"><span>Home</span><span class="on">Hosting ⌄</span><span>Services ⌄</span><span>Pricing</span><span>Contact Us</span></nav>
  <svg class="search" width="22" height="22" viewBox="0 0 22 22"><circle cx="9" cy="9" r="7" fill="none" stroke="#9aa1ab" stroke-width="2"/><path d="M14 14l6 6" stroke="#9aa1ab" stroke-width="2"/></svg>
  <div class="call">
    <svg width="34" height="34" viewBox="0 0 24 24"><path d="M5 3h4l2 5-3 2a12 12 0 0 0 6 6l2-3 5 2v4a2 2 0 0 1-2 2A18 18 0 0 1 3 5a2 2 0 0 1 2-2z" fill="none" stroke="#0a84de" stroke-width="1.4"/></svg>
    <div><b>(+1)555-019-274</b><small>Make a Call</small></div>
  </div>
  <span class="btn livechat">Live Chat</span>
</header>

<section class="abs hero">
  <h1>Think beyond<br>Share Host!</h1>
  <p>Here is the infographic which gives some insights about the type of Web hosting.</p>
  <div class="btns"><span class="btn">Get Started</span><span class="btn grey">Get in Touch</span></div>
  <div class="hero-art" role="img" aria-label="Illustration of a server rack, laptop, phone and cloud upload"></div>
</section>

<div class="abs dropdown">Shared Hosting<br>Cloud Hosting<br>Dedicated Hosting<br>Reseller Hosting<br>Contact Us<br>PanelPro Hosting<br>Vps Hosting</div>

<section class="abs pricing">
  <div class="wrap plans">
    <div class="plan">
      <h3>Personal <span>Plans</span></h3>
      <p class="desc">We take pride providing secure<br>Platform customers.</p>
      <div class="price-row"><div class="price"><s>$85</s><b>$49</b><small>/MO</small></div><div class="sale">On Sale<br><b>SAVE 49%</b></div></div>
      <ul class="specs-list">
        <li><svg width="10" height="10"><circle cx="5" cy="5" r="4.5" fill="none" stroke="#0a84de"/><path d="M3 5l1.5 1.5L7 3.5" stroke="#0a84de" fill="none"/></svg><span><b>CPU:</b> 2 Cores</span></li>
        <li><svg width="10" height="10"><circle cx="5" cy="5" r="4.5" fill="none" stroke="#0a84de"/><path d="M3 5l1.5 1.5L7 3.5" stroke="#0a84de" fill="none"/></svg><span><b>RAM:</b> 4 GB</span></li>
        <li><svg width="10" height="10"><circle cx="5" cy="5" r="4.5" fill="none" stroke="#0a84de"/><path d="M3 5l1.5 1.5L7 3.5" stroke="#0a84de" fill="none"/></svg><span><b>DISK:</b> (128GB - 256GB) SSD</span></li>
        <li><svg width="10" height="10"><circle cx="5" cy="5" r="4.5" fill="none" stroke="#0a84de"/><path d="M3 5l1.5 1.5L7 3.5" stroke="#0a84de" fill="none"/></svg><span><b>UPLINK:</b> 1Gbps - 20TB</span></li>
      </ul>
      <span class="btn">Purchase Now!</span>
    </div>
    <div class="plan">
      <h3>Standard <span>Plans</span></h3>
      <p class="desc">We take pride providing secure<br>Platform customers.</p>
      <div class="price-row"><div class="price"><s>$90</s><b>$75</b><small>/MO</small></div><div class="sale">On Sale<br><b>SAVE 49%</b></div></div>
      <ul class="specs-list">
        <li><svg width="10" height="10"><circle cx="5" cy="5" r="4.5" fill="none" stroke="#0a84de"/><path d="M3 5l1.5 1.5L7 3.5" stroke="#0a84de" fill="none"/></svg><span><b>CPU:</b> 4 Cores</span></li>
        <li><svg width="10" height="10"><circle cx="5" cy="5" r="4.5" fill="none" stroke="#0a84de"/><path d="M3 5l1.5 1.5L7 3.5" stroke="#0a84de" fill="none"/></svg><span><b>RAM:</b> 8 GB</span></li>
        <li><svg width="10" height="10"><circle cx="5" cy="5" r="4.5" fill="none" stroke="#0a84de"/><path d="M3 5l1.5 1.5L7 3.5" stroke="#0a84de" fill="none"/></svg><span><b>DISK:</b> (256GB - 500GB) SSD</span></li>
        <li><svg width="10" height="10"><circle cx="5" cy="5" r="4.5" fill="none" stroke="#0a84de"/><path d="M3 5l1.5 1.5L7 3.5" stroke="#0a84de" fill="none"/></svg><span><b>UPLINK:</b> 2Gbps - 40TB</span></li>
      </ul>
      <span class="btn">Purchase Now!</span>
    </div>
    <div class="plan">
      <h3>Business <span>Plans</span></h3>
      <p class="desc">We take pride providing secure<br>Platform customers.</p>
      <div class="price-row"><div class="price"><s>$95</s><b>$59</b><small>/MO</small></div><div class="sale">On Sale<br><b>SAVE 49%</b></div></div>
      <ul class="specs-list">
        <li><svg width="10" height="10"><circle cx="5" cy="5" r="4.5" fill="none" stroke="#0a84de"/><path d="M3 5l1.5 1.5L7 3.5" stroke="#0a84de" fill="none"/></svg><span><b>CPU:</b> 8 Cores</span></li>
        <li><svg width="10" height="10"><circle cx="5" cy="5" r="4.5" fill="none" stroke="#0a84de"/><path d="M3 5l1.5 1.5L7 3.5" stroke="#0a84de" fill="none"/></svg><span><b>RAM:</b> 16 GB</span></li>
        <li><svg width="10" height="10"><circle cx="5" cy="5" r="4.5" fill="none" stroke="#0a84de"/><path d="M3 5l1.5 1.5L7 3.5" stroke="#0a84de" fill="none"/></svg><span><b>DISK:</b> (500GB - 1TB) SSD</span></li>
        <li><svg width="10" height="10"><circle cx="5" cy="5" r="4.5" fill="none" stroke="#0a84de"/><path d="M3 5l1.5 1.5L7 3.5" stroke="#0a84de" fill="none"/></svg><span><b>UPLINK:</b> 4Gbps - 80TB</span></li>
      </ul>
      <span class="btn">Purchase Now!</span>
    </div>
  </div>
</section>

<section class="abs features">
  <div class="wrap">
    <h2 class="sec-title">We Provide <span class="blue">Hosting</span> Features</h2>
    <p class="sec-lead">Lorem ipsum dolor sit amet, consectetur adipiscing elit. Cras ut massa turpis. Phasellus eget tellus eros. Nulla ullamcorper sollicitudin velit, a porta mauris vestibulum ac. Nulla at tellus et arcu venenatis tempus.</p>
    <div class="feat-grid">
      <div class="feat"><div class="icon-ring"><svg width="40" height="40" viewBox="0 0 40 40"><circle cx="20" cy="20" r="14" fill="none" stroke="#0a84de" stroke-width="2"/><circle cx="20" cy="20" r="5" fill="none" stroke="#0a84de" stroke-width="2"/></svg></div><h4>Domain Sale</h4><p>Lorem ipsum dolor sit amet, consectetur adipiscing elit. Morbi porttitor ipsum ut efficitur commodo.</p></div>
      <div class="feat active"><div class="icon-ring"><svg width="40" height="40" viewBox="0 0 40 40"><path d="M10 26a7 7 0 0 1 2-13 9 9 0 0 1 17 2 6 6 0 0 1 0 11z" fill="none" stroke="#0a84de" stroke-width="2"/></svg></div><h4>Cloud Hosting</h4><p>Lorem ipsum dolor sit amet, consectetur adipiscing elit. Morbi porttitor ipsum ut efficitur commodo.</p></div>
      <div class="feat"><div class="icon-ring"><svg width="40" height="40" viewBox="0 0 40 40"><circle cx="20" cy="20" r="13" fill="none" stroke="#0a84de" stroke-width="2"/><path d="M7 20h26M20 7c-6 7-6 19 0 26M20 7c6 7 6 19 0 26" fill="none" stroke="#0a84de" stroke-width="2"/></svg></div><h4>VPS Hosting</h4><p>Lorem ipsum dolor sit amet, consectetur adipiscing elit. Morbi porttitor ipsum ut efficitur commodo.</p></div>
      <div class="feat"><div class="icon-ring"><svg width="40" height="40" viewBox="0 0 40 40"><rect x="15" y="7" width="10" height="8" fill="none" stroke="#0a84de" stroke-width="2"/><rect x="6" y="25" width="10" height="8" fill="none" stroke="#0a84de" stroke-width="2"/><rect x="24" y="25" width="10" height="8" fill="none" stroke="#0a84de" stroke-width="2"/><path d="M20 15v5M11 25v-5h18v5" fill="none" stroke="#0a84de" stroke-width="2"/></svg></div><h4>Shared Hosting</h4><p>Lorem ipsum dolor sit amet, consectetur adipiscing elit. Morbi porttitor ipsum ut efficitur commodo.</p></div>
      <div class="feat"><div class="icon-ring"><svg width="40" height="40" viewBox="0 0 40 40"><rect x="8" y="9" width="24" height="18" fill="none" stroke="#0a84de" stroke-width="2"/><path d="M14 32h12M20 27v5" stroke="#0a84de" stroke-width="2"/></svg></div><h4>Linux Hosting</h4><p>Lorem ipsum dolor sit amet, consectetur adipiscing elit. Morbi porttitor ipsum ut efficitur commodo.</p></div>
      <div class="feat"><div class="icon-ring"><svg width="40" height="40" viewBox="0 0 40 40"><circle cx="20" cy="20" r="13" fill="none" stroke="#0a84de" stroke-width="2"/><path d="M7 20h26M20 7v26" stroke="#0a84de" stroke-width="2"/></svg></div><h4>Web Security</h4><p>Lorem ipsum dolor sit amet, consectetur adipiscing elit. Morbi porttitor ipsum ut efficitur commodo.</p></div>
    </div>
  </div>
</section>

<section class="abs specs">
  <div class="wrap">
    <h2 class="sec-title">Our Hosting <span class="blue">Specifications</span></h2>
    <p class="sec-lead">Lorem ipsum dolor sit amet, consectetur adipiscing elit. Cras ut massa turpis. Phasellus eget tellus eros. Nulla ullamcorper sollicitudin velit, a porta mauris vestibulum ac.</p>
    <div class="spec-body">
      <div class="tabs"><div class="tab">Hosting Software</div><div class="tab">Hosting Database</div><div class="tab on">Additional Software</div><div class="tab">Hosting Security</div></div>
      <div class="spec-grid">
        <div class="spec"><svg width="46" height="46" viewBox="0 0 46 46"><rect x="4" y="10" width="38" height="26" fill="none" stroke="#0a84de" stroke-width="1.6"/><circle cx="23" cy="23" r="7" fill="none" stroke="#0a84de" stroke-width="1.6"/></svg><div><h5>1-Click App Marketplace</h5><p>Lorem ipsum dolor sit amet, consectetur adipiscing elit. Morbi porttitor ipsum ut efficitur commodo.</p></div></div>
        <div class="spec"><svg width="46" height="46" viewBox="0 0 46 46"><circle cx="23" cy="20" r="13" fill="none" stroke="#0a84de" stroke-width="1.6"/><path d="M10 20h26M23 7v26M8 40h30" stroke="#0a84de" stroke-width="1.6"/></svg><div><h5>Global Availability</h5><p>Lorem ipsum dolor sit amet, consectetur adipiscing elit. Morbi porttitor ipsum ut efficitur commodo.</p></div></div>
        <div class="spec"><svg width="46" height="46" viewBox="0 0 46 46"><rect x="4" y="10" width="38" height="26" fill="none" stroke="#0a84de" stroke-width="1.6"/><circle cx="23" cy="23" r="7" fill="none" stroke="#0a84de" stroke-width="1.6"/></svg><div><h5>Hostnotes in Minutes</h5><p>Lorem ipsum dolor sit amet, consectetur adipiscing elit. Morbi porttitor ipsum ut efficitur commodo.</p></div></div>
        <div class="spec"><svg width="46" height="46" viewBox="0 0 46 46"><circle cx="23" cy="20" r="13" fill="none" stroke="#0a84de" stroke-width="1.6"/><path d="M10 20h26M23 7v26M8 40h30" stroke="#0a84de" stroke-width="1.6"/></svg><div><h5>Flexible Compute Types</h5><p>Lorem ipsum dolor sit amet, consectetur adipiscing elit. Morbi porttitor ipsum ut efficitur commodo.</p></div></div>
      </div>
    </div>
  </div>
</section>

<section class="abs services">
  <div class="wrap">
    <h2 class="sec-title">We Provide <span class="blue">Best</span> Services</h2>
    <p class="sec-lead">Lorem ipsum dolor sit amet, consectetur adipiscing elit. Cras ut massa turpis. Phasellus eget tellus eros. Nulla ullamcorper sollicitudin velit, a porta mauris vestibulum ac. Nulla at tellus et arcu venenatis tempus.</p>
    <div class="svc-grid">
      <div class="svc"><h4>Automatic Scalability</h4><div class="dot"><svg width="40" height="40" viewBox="0 0 40 40"><circle cx="20" cy="20" r="12" fill="none" stroke="#fff" stroke-width="2"/><circle cx="20" cy="20" r="4" fill="#fff"/></svg></div><p>Lorem ipsum dolor sit amet, consectetur adipiscing elit. Morbi porttitor ipsum ut efficitur commodo.</p><a>Read More..</a></div>
      <div class="svc"><h4>E-Mail Hosting</h4><div class="dot"><svg width="40" height="40" viewBox="0 0 40 40"><rect x="8" y="8" width="24" height="8" fill="none" stroke="#fff" stroke-width="2"/><rect x="8" y="19" width="24" height="8" fill="none" stroke="#fff" stroke-width="2"/><path d="M12 31h16" stroke="#fff" stroke-width="2"/></svg></div><p>Lorem ipsum dolor sit amet, consectetur adipiscing elit. Morbi porttitor ipsum ut efficitur commodo.</p><a>Read More..</a></div>
      <div class="svc"><h4>Daily Backup</h4><div class="dot"><svg width="40" height="40" viewBox="0 0 40 40"><rect x="8" y="8" width="20" height="24" fill="none" stroke="#fff" stroke-width="2"/><path d="M12 14h12M12 19h12M12 24h8" stroke="#fff" stroke-width="2"/></svg></div><p>Lorem ipsum dolor sit amet, consectetur adipiscing elit. Morbi porttitor ipsum ut efficitur commodo.</p><a>Read More..</a></div>
    </div>
    <div class="dots"><i></i><i class="wide"></i><i></i></div>
  </div>
</section>

<section class="abs process">
  <div class="wrap">
    <h2 class="sec-title">Website Hosting <span class="blue">Process</span></h2>
    <p class="sec-lead">Lorem ipsum dolor sit amet, consectetur adipiscing elit. Cras ut massa turpis. Phasellus eget tellus eros. Nulla ullamcorper sollicitudin.</p>
    <div class="steps">
      <div class="step"><div class="circle"><svg width="40" height="40" viewBox="0 0 40 40"><rect x="6" y="10" width="28" height="20" fill="none" stroke="#fff" stroke-width="1.6"/><circle cx="20" cy="20" r="5" fill="none" stroke="#fff" stroke-width="1.6"/></svg><span class="num">1</span></div><h4>Register Domain Name</h4><p>Lorem ipsum dolor sit amet, consectetur adipiscing elit. Morbi porttitor ipsum ut efficitur commodo.</p></div>
      <div class="step"><div class="circle"><svg width="40" height="40" viewBox="0 0 40 40"><rect x="6" y="10" width="28" height="20" fill="none" stroke="#fff" stroke-width="1.6"/><circle cx="20" cy="20" r="5" fill="none" stroke="#fff" stroke-width="1.6"/></svg><span class="num">2</span></div><h4>Hosting A Website</h4><p>Lorem ipsum dolor sit amet, consectetur adipiscing elit. Morbi porttitor ipsum ut efficitur commodo.</p></div>
      <div class="step"><div class="circle"><svg width="40" height="40" viewBox="0 0 40 40"><rect x="6" y="10" width="28" height="20" fill="none" stroke="#fff" stroke-width="1.6"/><circle cx="20" cy="20" r="5" fill="none" stroke="#fff" stroke-width="1.6"/></svg><span class="num">3</span></div><h4>Upload Website To Server</h4><p>Lorem ipsum dolor sit amet, consectetur adipiscing elit. Morbi porttitor ipsum ut efficitur commodo.</p></div>
      <svg class="arrow" style="left:245px" width="130" height="40" viewBox="0 0 130 40"><path d="M4 30C40 0 90 0 124 34" fill="none" stroke="#16202e" stroke-width="1.5" stroke-dasharray="4 4"/><path d="M116 30l8 4-2-9" fill="none" stroke="#16202e" stroke-width="1.5"/></svg>
      <svg class="arrow" style="left:578px" width="130" height="40" viewBox="0 0 130 40"><path d="M4 10C40 40 90 40 124 6" fill="none" stroke="#16202e" stroke-width="1.5" stroke-dasharray="4 4"/><path d="M116 6l8 0-1 8" fill="none" stroke="#16202e" stroke-width="1.5"/></svg>
    </div>
  </div>
</section>

<section class="abs guarantee">
  <h2>30 Days Money-Back Guarantee</h2>
  <p>If you're not 100% satisfied with NimbaVault, we'll refund your payment. No hassle, no risk.</p>
  <span class="btn">Read More</span>
</section>

<section class="abs clients">
  <div class="wrap">
    <h2 class="sec-title">What Our <span class="blue">Clients</span> Says</h2>
    <p class="sec-lead">Lorem ipsum dolor sit amet, consectetur adipiscing elit. Cras ut massa turpis. Phasellus eget tellus eros. Nulla ullamcorper sollicitudin velit.</p>
    <div class="quotes">
      <div class="quote"><h5>John Doe</h5><small>CEO, ORCHARD CO</small><div class="avatar" role="img" aria-label="Client portrait photo"></div><p>Lorem ipsum dolor sit amet, consectetur adipiscing elit. Nunc faucibus, erat vitae commodo varius, ex velit pretium ipsum, cursus cursus ipsum nisl nec augue. quis malesuada quam aliquet et.</p><span class="mark">”</span></div>
      <div class="quote"><h5>John Doe</h5><small>CEO, ORCHARD CO</small><div class="avatar" role="img" aria-label="Client portrait photo"></div><p>Lorem ipsum dolor sit amet, consectetur adipiscing elit. Nunc faucibus, erat vitae commodo varius, ex velit pretium ipsum, cursus cursus ipsum nisl nec augue. quis malesuada quam aliquet et.</p><span class="mark">”</span></div>
      <div class="quote"><h5>John Doe</h5><small>CEO, ORCHARD CO</small><div class="avatar" role="img" aria-label="Client portrait photo"></div><p>Lorem ipsum dolor sit amet, consectetur adipiscing elit. Nunc faucibus, erat vitae commodo varius, ex velit pretium ipsum, cursus cursus ipsum nisl nec augue. quis malesuada quam aliquet et.</p><span class="mark">”</span></div>
    </div>
    <div class="dots"><i></i><i class="wide"></i><i></i></div>
  </div>
</section>

<footer class="abs footer">
  <div class="fcol about"><span class="logo">NimbaVault</span><p>Lorem ipsum dolor sit amet, consectetur adipiscing elit. Cras ut massa turpis. Phasellus eget tellus eros. Nulla ullamcorper sollicitudin velit, a porta mauris vestibulum ac.</p>
    <div class="cards"><span>Cardia</span><span>Paxo</span><span>Vendi</span><span>Rupo</span></div></div>
  <div class="fcol" style="left:321px"><h6>Our Services</h6><ul><li>SitePress Hosting</li><li>Shared Hosting</li><li>Dedicated Hosting</li><li>Managed Hosting</li><li>Cloud Hosting</li><li>Reseller Hosting</li></ul></div>
  <div class="fcol" style="left:554px"><h6>Quick Links</h6><ul><li>Terms of Service</li><li>Privacy Policy</li><li>FAQ</li><li>Contact Us</li><li>Support Center</li><li>Knowledgebase</li></ul></div>
  <div class="fcol" style="left:774px"><h6>Security</h6><ul><li>Terms of Service</li><li>Privacy Policy</li><li>FAQ</li><li>Contact Us</li><li>Support Center</li><li>Knowledgebase</li></ul></div>
  <div class="fcol contact" style="left:953px;width:220px"><h6>Contact</h6><ul>
    <li><svg width="12" height="14" viewBox="0 0 12 14"><path d="M6 13S1 8 1 5a5 5 0 0 1 10 0c0 3-5 8-5 8z" fill="#fff"/></svg><span>412 Harbor Lane, Fairview Heights, US</span></li>
    <li><svg width="12" height="12" viewBox="0 0 24 24"><path d="M5 3h4l2 5-3 2a12 12 0 0 0 6 6l2-3 5 2v4a2 2 0 0 1-2 2A18 18 0 0 1 3 5a2 2 0 0 1 2-2z" fill="#fff"/></svg><span>+1-555-019-274</span></li>
    <li><svg width="12" height="10" viewBox="0 0 12 10"><rect width="12" height="10" fill="#fff"/></svg><span>hello@nimbavault.test</span></li></ul></div>
</footer>

<div class="abs footbar"><span>Copyright 2021 NimbaVault All Rights Reserved.</span><div class="social"><i></i><i></i><i></i><i></i></div></div>

</body>
</html>
```